Harborline Renewal Business Card Design

Professional and clean design. The design colors should flow with the logo. Two-sided card with the website on the back which is:

www.HarborlineRenewal.example.

"Specializing in Water Damage Restoration"

On the front I need the name, email, phone, and logo.

Name: Darnell Quisby
Email: Darnell@HarborlineRenewal.example
Phone: 555-318-2046 for now

I only have the Preview and Thumbnail right now but should have the source files uploaded within a day or two.

Target Market(s)

Flood victims, home owners with water damage from busted pipes etc...

Industry/Entity Type

Business

Contact Information for Business Card

Name: Darnell Quisby

Font styles to use
Serif
Sans Serif

Requirements
Must have
• Business Card Details Info

```html
<!DOCTYPE html>
<html lang="en">
<head>
<meta charset="utf-8">
<title>Harborline Renewal Business Card</title>
<link href="https://fonts.googleapis.com/css2?family=Tinos:wght@400;700&display=swap" rel="stylesheet">
<style>
  :root {
    --page: #2b2c2e;
    --card: #ffffff;
    --blue: #2a8fd4;
    --blue-light: #5cc3ec;
    --ink: #4a4a4a;
    --mark-faint: #e9f1f7;
  }
  * { margin: 0; padding: 0; box-sizing: border-box; }
  html, body { width: 1200px; height: 900px; overflow: hidden; background: var(--page); }
  .canvas { position: relative; width: 1200px; height: 900px; }
  .card {
    position: absolute; left: 250px; width: 700px; height: 400px;
    background: var(--card); overflow: hidden;
    font-family: "Tinos", "Times New Roman", serif;
  }
  .card--back { top: 40px; }
  .card--front { top: 460px; }
  .card-art { position: absolute; inset: 0; width: 700px; height: 400px; }
  .brand { position: absolute; display: flex; align-items: center; gap: 14px; }
  .brand-dot { width: 54px; height: 54px; border-radius: 50%; background: var(--blue); flex: none; }
  .brand-name { font-size: 30px; font-weight: 400; color: var(--blue); letter-spacing: 2px; text-transform: uppercase; line-height: 1.05; }
  .card--back .brand { left: 60px; top: 220px; }
  .card--front .brand { left: 80px; top: 110px; }
  .tagline { position: absolute; right: 70px; top: 62px; text-align: right; color: var(--ink); }
  .tagline .site { font-size: 15px; }
  .tagline .spec { font-size: 19px; font-weight: 700; margin-top: 6px; }
  .holder { position: absolute; left: 80px; top: 300px; font-size: 24px; font-weight: 700; color: var(--blue-light); text-transform: uppercase; letter-spacing: 1px; }
  .contact { position: absolute; right: 40px; top: 225px; list-style: none; color: var(--ink); font-size: 17px; }
  .contact li { display: flex; align-items: center; gap: 8px; margin-bottom: 6px; }
  .contact svg { width: 14px; height: 14px; flex: none; }
</style>
</head>
<body>
<div class="canvas">

  <section class="card card--back">
    <svg class="card-art" viewBox="0 0 700 400" aria-hidden="true">
      <circle cx="560" cy="190" r="150" fill="none" stroke="var(--mark-faint)" stroke-width="16"/>
      <path d="M0 372 L420 372 C440 372 440 352 470 352 L700 352 L700 400 L0 400 Z" fill="var(--blue)"/>
      <path d="M470 352 L700 352 L700 336 L480 336 C455 336 455 352 470 352 Z" fill="var(--blue-light)"/>
    </svg>
    <div class="tagline">
      <p class="site">www.HarborlineRenewal.example</p>
      <p class="spec">Specializing in Water Damage Restoration</p>
    </div>
    <div class="brand">
      <span class="brand-dot"></span>
      <span class="brand-name">Harborline<br>Renewal</span>
    </div>
  </section>

  <section class="card card--front">
    <svg class="card-art" viewBox="0 0 700 400" aria-hidden="true">
      <circle cx="590" cy="190" r="150" fill="none" stroke="var(--mark-faint)" stroke-width="16"/>
      <path d="M0 375 L320 375 C345 375 350 355 380 355 L700 320 L700 400 L0 400 Z" fill="var(--blue)"/>
      <path d="M380 355 L700 320 L700 305 L390 340 C370 342 365 355 380 355 Z" fill="var(--blue-light)"/>
    </svg>
    <div class="brand">
      <span class="brand-dot"></span>
      <span class="brand-name">Harborline<br>Renewal</span>
    </div>
    <p class="holder">Darnell Quisby</p>
    <ul class="contact">
      <li>
        <svg viewBox="0 0 16 16"><path d="M3 1 L6 1 L7 5 L5 6.5 C6 9 7 10 9.5 11 L11 9 L15 10 L15 13 C15 14 14 15 13 15 C6 15 1 10 1 3 C1 2 2 1 3 1 Z" fill="var(--blue)"/></svg>
        555-318-2046
      </li>
      <li>
        <svg viewBox="0 0 16 16"><rect x="1" y="3" width="14" height="10" rx="1" fill="var(--blue)"/><path d="M1.5 4 L8 9 L14.5 4" fill="none" stroke="#fff" stroke-width="1.3"/></svg>
        Darnell@HarborlineRenewal.example
      </li>
    </ul>
  </section>

</div>
</body>
</html>
```